Company identity deisgn should support 2 languages

I would like to get our company identity design
This includes the following only
Business Cards 2 languages Arabic and English
Email signature
Letterhead
Linkedin profile images
Attached is the logo in Ai format

Requirements
Must have
• For business card
Must have
Name and Adrees in arabic
Name and Address in english
You might use both side of the card
Should not have
• Any pictures other than the logo

```html
<!DOCTYPE html>
<html lang="en">
<head>
<meta charset="utf-8">
<title>Nova Logic Systems – Business Card</title>
<link rel="stylesheet" href="https://fonts.googleapis.com/css2?family=Montserrat:wght@400;500;600;700&family=Cairo:wght@400;600;700&display=swap">
<style>
  :root {
    --brand-blue: #1b6fb6;
    --ink: #4a4a4a;
    --muted: #9a9a9a;
    --band-grey: #d6d6d6;
    --peak-grey: #5a5a5a;
    --paper: #ffffff;
  }
  * { margin: 0; padding: 0; box-sizing: border-box; }
  html, body { width: 1200px; height: 578px; overflow: hidden; background: var(--paper); }
  .card {
    position: relative;
    width: 1200px;
    height: 578px;
    background: var(--paper);
    font-family: "Montserrat", sans-serif;
    color: var(--ink);
  }
  .holder { position: absolute; left: 70px; top: 48px; }
  .holder__name {
    font-weight: 700;
    font-size: 35px;
    letter-spacing: 0.5px;
    color: var(--brand-blue);
    line-height: 1;
  }
  .holder__role {
    font-size: 23px;
    color: var(--muted);
    margin-top: 12px;
    line-height: 1;
  }
  .holder__name-ar, .holder__role-ar {
    font-family: "Cairo", sans-serif;
    direction: rtl;
    text-align: left;
  }
  .holder__name-ar {
    font-weight: 700;
    font-size: 34px;
    color: var(--brand-blue);
    line-height: 1.1;
    margin-top: 6px;
  }
  .holder__role-ar {
    font-size: 24px;
    color: var(--muted);
    line-height: 1.1;
  }
  .address-ar {
    position: absolute;
    right: 98px;
    top: 38px;
    font-family: "Cairo", sans-serif;
    direction: rtl;
    text-align: right;
    color: var(--ink);
  }
  .address-ar__line1 { font-size: 25px; line-height: 1.3; }
  .address-ar__line2 { font-size: 21px; line-height: 1.5; }
  .address-en {
    position: absolute;
    left: 770px;
    top: 130px;
    font-size: 25px;
    line-height: 46px;
    color: var(--ink);
  }
  .company {
    position: absolute;
    left: 416px;
    top: 262px;
    display: flex;
    align-items: center;
    gap: 26px;
  }
  .company__square {
    width: 96px;
    height: 96px;
    background: var(--brand-blue);
  }
  .company__names { color: var(--muted); font-weight: 600; }
  .company__name {
    font-size: 40px;
    letter-spacing: 3px;
    line-height: 1.1;
  }
  .company__name-ar {
    font-family: "Cairo", sans-serif;
    font-weight: 600;
    font-size: 26px;
    direction: rtl;
    text-align: right;
    letter-spacing: 2px;
    line-height: 1.4;
  }
  .contacts {
    position: absolute;
    left: 60px;
    right: 98px;
    top: 422px;
    display: flex;
    justify-content: space-between;
    font-size: 23px;
    color: var(--ink);
  }
  .contacts__item { display: flex; align-items: center; gap: 6px; }
  .contacts__icon { width: 22px; height: 22px; fill: var(--brand-blue); flex: none; }
  .footer-band { position: absolute; left: 0; top: 484px; width: 1200px; height: 50px; }
  .footer-band__url {
    position: absolute;
    left: 0;
    width: 900px;
    top: 0;
    height: 50px;
    line-height: 50px;
    text-align: center;
    color: var(--paper);
    font-size: 22px;
    font-weight: 500;
    letter-spacing: 4px;
  }
</style>
</head>
<body>
<main class="card">
  <section class="holder">
    <h1 class="holder__name">DANIEL HARPER</h1>
    <p class="holder__role">President</p>
    <p class="holder__name-ar" lang="ar">دانيال هاربر</p>
    <p class="holder__role-ar" lang="ar">رئيس</p>
  </section>

  <address class="address-ar" lang="ar">
    <p class="address-ar__line1">1429 ويلو كرست درايف</p>
    <p class="address-ar__line2">فيربانكس، ألاسكا 99712</p>
  </address>

  <address class="address-en" style="font-style:normal">
    <p>1429 Willow Crest Drive</p>
    <p>Fairbanks, Alaska 99712</p>
  </address>

  <div class="company">
    <span class="company__square"></span>
    <div class="company__names">
      <p class="company__name">NOVA LOGIC SYSTEMS</p>
      <p class="company__name-ar" lang="ar">شركة أنظمة نوفا لوجيك</p>
    </div>
  </div>

  <ul class="contacts" style="list-style:none">
    <li class="contacts__item">
      <svg class="contacts__icon" viewBox="0 0 24 24"><path d="M6.6 10.8a15.1 15.1 0 0 0 6.6 6.6l2.2-2.2c.3-.3.7-.4 1-.2 1.1.4 2.3.6 3.6.6.6 0 1 .4 1 1V20c0 .6-.4 1-1 1A17 17 0 0 1 3 4c0-.6.4-1 1-1h3.5c.6 0 1 .4 1 1 0 1.3.2 2.5.6 3.6.1.3 0 .7-.2 1z"/></svg>
      555-214-7730
    </li>
    <li class="contacts__item">
      <svg class="contacts__icon" viewBox="0 0 24 24"><path d="M7 1h10a2 2 0 0 1 2 2v18a2 2 0 0 1-2 2H7a2 2 0 0 1-2-2V3a2 2 0 0 1 2-2zm0 3v14h10V4zm5 15.2a1.2 1.2 0 1 0 0 2.4 1.2 1.2 0 0 0 0-2.4z"/></svg>
      555-318-6642
    </li>
    <li class="contacts__item">
      <svg class="contacts__icon" viewBox="0 0 24 24"><path d="M6 2h12v5H6zM4 8h16a2 2 0 0 1 2 2v7h-4v5H6v-5H2v-7a2 2 0 0 1 2-2zm4 7v5h8v-5z"/></svg>
      555-407-2291
    </li>
    <li class="contacts__item">
      <svg class="contacts__icon" viewBox="0 0 24 24"><path d="M2 5h20v14H2zm2 2v.4l8 5.4 8-5.4V7z"/></svg>
      info@novalogicsystems.com
    </li>
  </ul>

  <div class="footer-band">
    <svg width="1200" height="50" viewBox="0 0 1200 50">
      <polygon points="0,0 896,0 880,50 0,50" fill="var(--brand-blue)"/>
      <polygon points="938,0 1200,0 1200,50 922,50" fill="var(--band-grey)"/>
      <polygon points="906,0 928,0 944,50 890,50" fill="var(--peak-grey)"/>
    </svg>
    <p class="footer-band__url">WWW.NOVALOGICSYSTEMS.COM</p>
  </div>
</main>
</body>
</html>
```